Summit Ridge Business Card

Side 1: Summit Ridge Logo (logo without Maltese cross) with industrial rope rescue related theme. Our company services - TRAINING - Fire Training, Confined Space Rescue Training, Rope Rescue training, Hazmat Training, Incident Command, EMS, Pump Operations Training. Website - summitridgeexample.com.
Side 2: Summit Ridge Fire Department Logo (logo with Maltese cross) with Firefighter related theme. Company (division) services - FIELD SERVICES - Fire Department, Stand-by Rescue, Safety, EMS, Planning. "Supporting the Emergency Response Community Since 1967"

Add contact information wherever it makes since (Name, Email, Phone).
I would like it to represent the Summit Ridge Fire Department Logo as a division not as a separate entity without saying it, possibly by depicting it in the background of Side 2 instead of being a standalone picture like the logo on Side 1.

```html
<!DOCTYPE html>
<html lang="en">
<head>
<meta charset="utf-8">
<title>Summit Ridge Business Card</title>
<link rel="stylesheet" href="https://fonts.googleapis.com/css2?family=Poppins:wght@400;500;600;700&display=swap">
<style>
  :root {
    --red: #f60000;
    --red-deep: #e20000;
    --red-faint: #e80000;
    --white: #ffffff;
    --ink: #1d1d1f;
    --backdrop: #c9c9c9;
  }
  * { box-sizing: border-box; margin: 0; padding: 0; }
  html, body { width: 1200px; height: 800px; overflow: hidden; }
  body {
    background: var(--backdrop);
    font-family: "Poppins", sans-serif;
    display: flex;
    flex-direction: column;
    align-items: center;
    justify-content: center;
    gap: 36px;
  }
  .card {
    position: relative;
    width: 620px;
    height: 354px;
    overflow: hidden;
    box-shadow: 0 10px 28px rgba(0,0,0,0.25);
  }

  /* Field services side */
  .card--field { background: var(--red); color: var(--white); }
  .division-mark {
    position: absolute;
    left: 120px; top: 18px;
    font-weight: 700;
    font-size: 64px;
    line-height: 1;
    color: var(--red-faint);
    letter-spacing: 2px;
    white-space: nowrap;
  }
  .contact {
    position: absolute;
    left: 150px; top: 40px;
    text-align: left;
  }
  .contact__name { font-weight: 600; font-size: 26px; letter-spacing: 0.5px; }
  .contact__rule { width: 60px; height: 1px; background: var(--white); margin: 8px 0 8px 40px; }
  .contact__line { font-size: 15px; line-height: 1.35; }
  .field-block {
    position: absolute;
    left: 0; right: 0; top: 176px;
    padding: 0 34px;
  }
  .field-block__rule { height: 1px; background: var(--white); }
  .field-block__rule--short { margin-left: 70px; }
  .field-services {
    font-weight: 700;
    text-transform: uppercase;
    letter-spacing: 1px;
    font-size: 25px;
    line-height: 1.2;
    padding: 12px 0 10px 8px;
  }
  .field-services span { display: block; }
  .field-services span + span { padding-left: 118px; }
  .field-tagline {
    font-size: 15px;
    font-weight: 500;
    letter-spacing: 0.4px;
    padding: 10px 0 0 94px;
  }

  /* Training side */
  .card--training { background: var(--white); color: var(--ink); }
  .brand {
    position: absolute;
    right: 38px; top: 108px;
    display: flex;
    align-items: center;
    gap: 12px;
  }
  .brand__square { width: 22px; height: 22px; background: var(--red); }
  .brand__name {
    font-weight: 700;
    font-size: 36px;
    color: var(--red);
    text-transform: uppercase;
    letter-spacing: 1px;
  }
  .services {
    position: absolute;
    left: 40px; top: 36px;
    list-style: none;
    text-transform: uppercase;
    font-weight: 500;
    font-size: 15.5px;
    letter-spacing: 0.8px;
    line-height: 1.72;
  }
  .services li { display: flex; align-items: center; gap: 10px; }
  .services li::before {
    content: "";
    width: 8px; height: 8px;
    border-radius: 50%;
    background: var(--red);
    flex: none;
  }
  .web-band {
    position: absolute;
    left: 0; right: 0; bottom: 0;
    height: 66px;
    background: var(--red);
    color: var(--white);
    display: flex;
    align-items: center;
    justify-content: center;
    font-size: 19px;
    font-weight: 500;
    letter-spacing: 3px;
  }
</style>
</head>
<body>
  <section class="card card--field" aria-label="Summit Ridge Fire Department field services side">
    <div class="division-mark" aria-hidden="true">SUMMIT RIDGE</div>
    <div class="contact">
      <p class="contact__name">Daniel Hartley</p>
      <div class="contact__rule"></div>
      <p class="contact__line">044-555 010 234</p>
      <p class="contact__line">info@summitridgeexample.com</p>
    </div>
    <div class="field-block">
      <div class="field-block__rule"></div>
      <p class="field-services">
        <span>Fire Department • Stand-by Rescue</span>
        <span>Safety • EMS • Planning</span>
      </p>
      <div class="field-block__rule field-block__rule--short"></div>
      <p class="field-tagline">Supporting the Emergency Response Community Since 1967</p>
    </div>
  </section>

  <section class="card card--training" aria-label="Summit Ridge training side">
    <ul class="services">
      <li>Fire Training</li>
      <li>Confined Space Rescue Training</li>
      <li>Rope Rescue Training</li>
      <li>Hazmat Training</li>
      <li>Incident Command</li>
      <li>EMS</li>
      <li>Pump Operations Training</li>
    </ul>
    <div class="brand">
      <span class="brand__square"></span>
      <span class="brand__name">Summit Ridge</span>
    </div>
    <div class="web-band">www.summitridgeexample.com</div>
  </section>
</body>
</html>
```